SEO and image area for top of invitation website

We need to add an area on our final category pages for SEO text. Instead of just adding text, we'd like to develop a graphical approach that keeps with our soft, feminine look.

You can view an example of our current final category page at http://www.cardwrenpress.example/invitations/boy-birthday

I've attached an image of what we're thinking it could look like, but you're welcome to alter the design.

The area should be the same width as our site, but can be any height you determine appropriate.

The winner of this project may be approached to develop the additional designs and backgrounds for us as another project. We additionally have several other projects we're interested in doing with the winner.
Updates

We have had a question about the right side of the banner, and what "Free Unlimited Proofs" mean.

About Free Unlimited Proofs:

We are a custom invitation printing company. When a customer orders an invitation from us, they tell us what information we want on the invitation. We then create an electronic sample, or "proof", of what it will look like. We then email it to the customer and they can tell us if they want to make any more changes. We will continue to send them samples, or what we call "proofs", until they are completely satisfied with the way it looks.

We offer Free UNLIMITED Proofs. Compared to our competitors, we are the only one to offer free unlimited proofs.

So, for the right side of this banner, we need an image, or a badge, promoting that we offer free unlimited proofs, and you can include that we are the only ones to do it, if your design has space for that information.

Also, keep in mind, that for other category pages, we may create different images or badges to put in this area - such as for our Low Price Guarantee or to promote a coupon or specific product, for example. So, your design should be able to work with various images on the right side.

Target Market(s)

Our demographic is 100% women, ages 25-60.

Industry/Entity Type

Seo

Requirements
Must have
• The area must have 3 things:
1) Area for the title of the page.
2) Area for SEO text describing the category page.
3) Area for an image. Keep in mind that this image may change for each category page. For this project, you will create an image for our offering of "Free Unlimited Proofs". On other pages, we may display other images we create such as "Low Price Guarantee" or images of certain products we'd like to promote. Just keep this in mind when you're making the design flow.
Nice to have
• Optional: Light design background. We wouldn't mind there being a slight graphical background to this area, to keep it interesting to the eye. Then, for other category pages, we may make additional backgrounds to use in this box area.

```html
<!DOCTYPE html>
<html lang="en">
<head>
<meta charset="utf-8">
<title>Boy Birthday Cards – Category Banner</title>
<link rel="stylesheet" href="https://fonts.googleapis.com/css2?family=Kreon:wght@400;500&family=Alegreya+SC:wght@700;800&display=swap">
<style>
  :root {
    --canvas: #ffffff;
    --frame-border: #bdbdbd;
    --pattern-gray: #dcdcdc;
    --mauve: #776870;
    --mauve-dark: #5f5259;
    --sun: #f6cd4c;
    --white: #ffffff;
  }
  * { box-sizing: border-box; margin: 0; padding: 0; }
  html, body {
    width: 1200px; height: 261px; overflow: hidden;
    background: var(--canvas);
  }
  .category-banner {
    position: relative;
    width: 1200px; height: 261px;
  }
  .banner-backdrop {
    position: absolute;
    left: 11px; top: 11px; width: 1178px; height: 242px;
    border-radius: 14px;
    background: var(--pattern-gray);
    border: 2px solid var(--frame-border);
    box-shadow: 0 1px 3px rgba(0,0,0,0.25);
  }
  .page-title {
    position: absolute;
    left: 13px; top: 13px; width: 443px; height: 64px;
    background: var(--mauve);
    border-top-left-radius: 12px;
    color: var(--sun);
    font-family: "Kreon", Georgia, serif;
    font-weight: 400;
    font-size: 36px;
    line-height: 64px;
    padding-left: 20px;
    letter-spacing: 0.3px;
  }
  .seo-text {
    position: absolute;
    left: 24px; top: 93px; width: 865px; height: 141px;
    background: var(--mauve);
    border-radius: 9px;
    box-shadow: 0 1px 2px rgba(0,0,0,0.2);
    padding: 10px 14px 0 16px;
    color: var(--white);
    font-family: "Alegreya SC", Georgia, serif;
    font-weight: 700;
    font-size: 19.5px;
    line-height: 27px;
  }
  .promo-badge {
    position: absolute;
    left: 917px; top: 19px; width: 256px; height: 210px;
  }
  .promo-headline {
    height: 99px;
    background: var(--sun);
    border-radius: 4px 4px 0 0;
    display: flex; align-items: center; justify-content: center;
    text-align: center;
    color: var(--mauve);
    font-family: "Alegreya SC", Georgia, serif;
    font-weight: 800;
    font-size: 24px;
    line-height: 31px;
  }
  .promo-details {
    position: relative;
    height: 111px;
    background: var(--mauve);
    border-radius: 0 0 4px 4px;
    padding: 8px 14px 0;
    text-align: center;
    color: var(--white);
    font-family: "Alegreya SC", Georgia, serif;
    font-weight: 700;
    font-size: 14px;
    line-height: 16px;
  }
  .promo-mascot {
    position: absolute;
    right: -12px; bottom: -14px;
    width: 44px; height: 40px;
    border-radius: 50%;
    background: var(--sun);
  }
</style>
</head>
<body>
  <section class="category-banner">
    <div class="banner-backdrop" role="img" aria-label="Light gray background with a soft repeating pattern of small ducks"></div>

    <h1 class="page-title">Boy Birthday Cards</h1>

    <p class="seo-text">Lorem ipsum dolor sit amet, consectetur adipiscing elit. Mauris sed tortor mauris, et mollis est. Curabitur lobortis neque ut ante venenatis mattis. Nullam nisl erat, suscipit eget viverra in, vestibulum eu mi. Integer elementum arcu magna, id porta odio.</p>

    <aside class="promo-badge">
      <div class="promo-headline">Free, Unlimited<br>&amp; Exclusive!</div>
      <div class="promo-details">
        We offer FREE unlimited proofs, making sure each and every card is just right! Something you won’t get anywhere else.
        <div class="promo-mascot" role="img" aria-label="Small yellow duck illustration"></div>
      </div>
    </aside>
  </section>
</body>
</html>
```